Flyer-Design für Ofenservice Firma
Zielgruppe
Die Firma hat als Kerngeschäft Wartung, Reinigung, Reparatur und Inbetriebnahme von Öfen und Kaminen aller Art. Der Fokus liegt dabei auf Pelletöfen. Die Firma versteht sich als zuverlässiger Dienstleister mit gutem Preisleistungsverhältnis. Zielgruppe sind hauptsächlich private Bewohner von Einfamilienhäusern in der ländlichen Gegend (Hessen)
Aufgabenstellung
Zur Bekanntmachung nach Neugründung soll ein Faltflyer gestaltet werden mit insgesamt 6 Bereichen. Die Informationen, welche auf den Flyer sollen, entnehmen Sie bitte dem Entwurf (flyer.pdf). Dieser stellt nur eine erste Idee dar und darf gerne nach Belieben verändert bzw. neu gestaltet werden. Die enthaltenen Informationen, sollten im Großen und Ganzen aber beibehalten werden. Schön wäre evtl. auch eine Hervorhebung der Preise, da wir Preisführer im Markt sind. Auch die Bilder unseres Teams sollen in den Flyer integriert sein. Auf Anfrage kann ich auch gerne weitere Kamin- und Ofenfotos zur Verfügung stellen, für welche ich die Nutzungsrechte habe. Falls Sie weitere Informationen benötigen oder Fragen haben, kommen Sie gerne auf mich zu. Die Bilder dürfen gerne etwas ausgeschnitten werden. Es geht in erster Linie darum, dass die Kunden erkennen, welche Art von Ofen sie zu Hause haben.

```html
<!DOCTYPE html>
<html lang="de">
<head>
<meta charset="utf-8">
<title>FLAMMWERK Ofenservice – Faltflyer</title>
<link href="https://fonts.googleapis.com/css2?family=Open+Sans:wght@400;600;700;800&display=swap" rel="stylesheet">
<style>
  :root {
    --stage: #ecebe8;
    --slate: #5b636b;
    --slate-dark: #4a5158;
    --ink: #5a6068;
    --text: #555b61;
    --orange: #d06a22;
    --white: #ffffff;
    --paper-grey: #f4f4f4;
  }
  * { box-sizing: border-box; margin: 0; padding: 0; }
  html, body {
    width: 1200px; height: 848px; overflow: hidden;
    background: var(--stage);
    font-family: "Open Sans", Arial, sans-serif;
  }
  .flyer {
    position: absolute; left: 107px; top: 70px;
    width: 995px; height: 709px;
    background: var(--slate);
    box-shadow: 0 4px 14px rgba(0,0,0,.25);
  }
  .panel { position: absolute; top: 0; height: 100%; }

  /* Innenseite links */
  .panel--intro {
    left: 0; top: 25px; width: 328px; height: 684px;
    background: linear-gradient(180deg, var(--white) 0%, var(--paper-grey) 100%);
    overflow: hidden;
  }
  .intro__brand { position: absolute; left: 30px; top: 40px; color: var(--ink); font-size: 18px; }
  .intro__brand strong { font-weight: 800; letter-spacing: .3px; }
  .intro__brand span { font-weight: 400; font-size: 16px; }
  .intro__claim {
    position: absolute; left: 30px; top: 64px; width: 280px;
    color: var(--ink); font-size: 15.5px; line-height: 20px;
  }
  .intro__copy {
    position: absolute; left: 30px; top: 128px; width: 275px;
    color: var(--text); font-size: 11.2px; line-height: 14px; text-align: justify;
    hyphens: auto;
  }
  .intro__copy p { margin-bottom: 14px; }
  .intro__copy b { font-weight: 700; color: #4a4f55; }
  .team-photo { position: absolute; left: 0; top: 0; width: 328px; height: 684px; }

  /* Mittelteil */
  .panel--services {
    left: 328px; width: 328px; color: var(--white); text-align: center;
  }
  .services__brand { margin-top: 58px; font-size: 21px; font-weight: 800; letter-spacing: .3px; line-height: 24px; }
  .services__sub { font-size: 14px; font-weight: 400; line-height: 17px; }
  .services__heading { margin-top: 20px; font-size: 11.5px; font-weight: 700; }
  .services__list { margin: 18px 20px 0; font-size: 11.5px; line-height: 16.2px; }
  .services__list p { margin-bottom: 16px; }
  .services__list b { font-weight: 700; }
  .contact { position: absolute; left: 0; right: 0; top: 490px; font-size: 13.5px; line-height: 19px; font-weight: 600; letter-spacing: .2px; }
  .contact__block { margin-bottom: 19px; }
  .contact__label { font-weight: 700; }

  /* Titelseite rechts */
  .panel--cover { left: 656px; width: 339px; background: var(--white); overflow: hidden; }
  .cover__logo {
    position: absolute; left: 0; right: 0; top: 86px; text-align: center;
    color: var(--ink); font-size: 27px; font-weight: 800; letter-spacing: 2px;
  }
  .cover__logo-mark {
    display: inline-block; width: 14px; height: 14px; border-radius: 50%;
    background: var(--ink); margin-right: 8px; vertical-align: 3px;
  }
  .cover__logo-sub { position: absolute; right: 68px; top: 110px; color: var(--ink); font-size: 14px; font-weight: 400; }
  .cover__art { position: absolute; left: 0; top: 0; }
  .cover__headline {
    position: absolute; left: 34px; top: 570px;
    color: var(--ink); font-size: 22px; font-weight: 800; line-height: 29px; letter-spacing: .2px;
  }
  .cover__url { position: absolute; left: 34px; top: 658px; color: var(--orange); font-size: 13.5px; font-weight: 700; }
</style>
</head>
<body>
<main class="flyer">

  <section class="panel panel--intro">
    <svg class="team-photo" viewBox="0 0 328 684" role="img" aria-label="Foto des Service-Teams: drei Mitarbeiter in dunkler Arbeitskleidung">
      <defs>
        <linearGradient id="teamTone" x1="0" y1="0" x2="0" y2="1">
          <stop offset="0" stop-color="#e9e9e9"/>
          <stop offset="0.45" stop-color="#b9b4ae"/>
          <stop offset="1" stop-color="#2e2e30"/>
        </linearGradient>
      </defs>
      <polygon points="0,440 328,338 328,684 0,684" fill="url(#teamTone)"/>
      <polygon points="0,428 328,330 328,338 0,440" fill="#ffffff"/>
    </svg>
    <div class="intro__brand"><strong>FLAMMWERK</strong> <span>Ofenservice</span></div>
    <div class="intro__claim">Ihr kompetenter Servicespezialist für Öfen aller Art.</div>
    <div class="intro__copy">
      <p>Als Inhaber geführtes Unternehmen bieten wir <b>professionelle Serviceleistungen rund um Öfen aller Art</b> (Kaminöfen, Pelletöfen, Scheitholzöfen, Kachelöfen, offene Kamine, Grund- und Speicheröfen).</p>
      <p>Durch erfahrene Mitarbeiter, regelmäßigen Personalschulungen und <b>Zusammenarbeit mit namhaften Herstellern</b> können wir ihnen eine breite Palette an Dienstleistungen rund um Kaminöfen bieten.</p>
      <p><b>Guter Service muss nicht teuer sein!</b> Überzeugen Sie sich von unserem <b>Preis-Leistungs-Verhältnis</b> sowie unseren <b>exklusiven Konditionen</b> bei Abschluss eines Wartungsvertrags.</p>
    </div>
  </section>

  <section class="panel panel--services">
    <div class="services__brand">FLAMMWERK</div>
    <div class="services__sub">Ofenservice</div>
    <div class="services__heading">Weitere Leistungen:</div>
    <div class="services__list">
      <p><b>Reparatur und Instandsetzung:</b> Funktioniert ihr Ofen nicht richtig, sind wir schnellstmöglich für Sie da und setzen ihren Ofen wieder instand.</p>
      <p><b>Inbetriebnahme:</b> Sie haben einen neuen Ofen erworben und möchten sich über die richtige Nutzung und Befeuerung informieren?</p>
      <p><b>Kaufberatung:</b> Sie planen eine Neuanschaffung und möchten sich vorab über Anschlussmöglichkeiten, Brennstoffarten und Modelle informieren? Wir beraten Sie unabhängig und auf Ihre Bedürfnisse zugeschnitten.</p>
    </div>
    <address class="contact" style="font-style:normal">
      <div class="contact__block">FLAMMWERK OFENSERVICE<br>Birkenweg 12<br>35390 Talheim</div>
      <div class="contact__block"><span class="contact__label">Telefon:</span><br>06400 / 312-45-67</div>
      <div class="contact__block"><span class="contact__label">Online:</span><br>info@flammwerk-ofenservice.de<br>www.flammwerk-ofenservice.de</div>
    </address>
  </section>

  <section class="panel panel--cover">
    <div class="cover__logo"><span class="cover__logo-mark"></span>FLAMMWERK</div>
    <div class="cover__logo-sub">Ofenservice</div>
    <svg class="cover__art" width="339" height="709" viewBox="0 0 339 709">
      <defs>
        <linearGradient id="fireTone" x1="0" y1="0" x2="1" y2="1">
          <stop offset="0" stop-color="#c9c3b8"/>
          <stop offset="0.55" stop-color="#a89a86"/>
          <stop offset="1" stop-color="#6b5a48"/>
        </linearGradient>
      </defs>
      <polygon points="0,190 339,138 339,166 0,193" fill="var(--orange)"/>
      <polygon points="0,193 339,166 339,475 0,507" fill="url(#fireTone)" role="img" aria-label="Foto eines Kamineinsatzes mit Feuer in heller Steinwand, daneben ein Holzkorb"/>
      <polygon points="0,507 339,475 339,482 0,531" fill="var(--orange)"/>
    </svg>
    <h1 class="cover__headline">IHR KOMPETENTER<br>SERVICESPEZIALIST<br>FÜR ÖFEN ALLER ART</h1>
    <div class="cover__url">www.flammwerk-ofenservice.de</div>
  </section>

</main>
</body>
</html>
```